Brivolt Technologies business card design

We need a business card designed with our new logo. it would be great if the card could communicate it is a technology based company.

Target Market(s)

system integrators

Industry/Entity Type

technology, IOT

Contact Information for Business Card

Name, designation, Address, telephone number, email address

Requirements
Must have
• logo and company name
Nice to have
• something to do with technology

```html
<!DOCTYPE html>
<html lang="en">
<head>
<meta charset="utf-8">
<title>Brivolt Technologies — Business Card</title>
<link rel="stylesheet" href="https://fonts.googleapis.com/css2?family=Open+Sans:wght@400;600;700&display=swap">
<style>
  :root {
    --backdrop: #3a3a3a;
    --card: #1b1b1b;
    --card-deep: #121212;
    --accent: #f39317;
    --ink: #ffffff;
    --muted: #d6d6d6;
  }
  * { box-sizing: border-box; margin: 0; padding: 0; }
  html, body { width: 1200px; height: 801px; overflow: hidden; }
  body {
    background: var(--backdrop);
    font-family: "Open Sans", sans-serif;
    display: flex; align-items: center; justify-content: center; gap: 40px;
  }
  .card {
    position: relative; width: 540px; height: 309px;
    background: var(--card);
    border-bottom: 3px solid var(--accent);
    overflow: hidden;
  }
  .brand { display: flex; align-items: center; gap: 10px; }
  .brand-square { width: 22px; height: 22px; background: var(--accent); }
  .brand-name { color: var(--ink); font-weight: 700; font-size: 24px; letter-spacing: 1px; text-transform: uppercase; }

  .front .brand { position: absolute; left: 36px; top: 108px; }
  .front .brand-mark-area {
    position: absolute; right: 40px; top: -20px; width: 200px; height: 170px;
    background: radial-gradient(circle at 50% 40%, #262626, #1b1b1b 70%);
  }
  .person { position: absolute; left: 36px; top: 170px; }
  .person-name { color: var(--accent); font-weight: 700; font-size: 20px; text-transform: uppercase; letter-spacing: .5px; }
  .person-role { color: var(--muted); font-size: 13px; margin-top: 2px; }
  .contact { position: absolute; left: 36px; bottom: 26px; list-style: none; }
  .contact li { display: flex; align-items: center; gap: 8px; color: var(--ink); font-size: 12.5px; line-height: 20px; }
  .contact svg { width: 12px; height: 12px; fill: var(--accent); flex: none; }
  .address { position: absolute; right: 30px; top: 170px; text-align: right; color: var(--ink); font-size: 12.5px; line-height: 19px; }

  .back .pattern-area {
    position: absolute; inset: 0;
    background: linear-gradient(135deg, var(--card-deep), #222 55%, #2a2a2a);
  }
  .back .brand { position: absolute; right: 48px; top: 140px; }
</style>
</head>
<body>
  <section class="card front">
    <div class="brand-mark-area" role="img" aria-label="Large faint embossed brand mark"></div>
    <div class="brand">
      <span class="brand-square"></span>
      <span class="brand-name">Brivolt Technologies</span>
    </div>
    <div class="person">
      <p class="person-name">Darian Kolwell</p>
      <p class="person-role">President</p>
    </div>
    <ul class="contact">
      <li><svg viewBox="0 0 24 24"><path d="M6.6 10.8a15 15 0 0 0 6.6 6.6l2.2-2.2a1 1 0 0 1 1-.25 11.4 11.4 0 0 0 3.6.57 1 1 0 0 1 1 1V20a1 1 0 0 1-1 1A17 17 0 0 1 3 4a1 1 0 0 1 1-1h3.5a1 1 0 0 1 1 1c0 1.25.2 2.45.57 3.6a1 1 0 0 1-.25 1z"/></svg>555-318-7024</li>
      <li><svg viewBox="0 0 24 24"><path d="M2 5h20v14H2z M2 5l10 7 10-7" /></svg>info@brivolttech.com</li>
      <li><svg viewBox="0 0 24 24"><circle cx="12" cy="12" r="10"/></svg>www.brivolttech.com</li>
    </ul>
    <p class="address">1870 Harborview Lane<br>Seacrest CA 90417</p>
  </section>

  <section class="card back">
    <div class="pattern-area" role="img" aria-label="Repeating spot-gloss pattern of the brand mark"></div>
    <div class="brand">
      <span class="brand-square"></span>
      <span class="brand-name">Brivolt</span>
    </div>
  </section>
</body>
</html>
```